Looking for someone to design a business card for my plumbing business Quandor Plumbing Solutions I want the background also to be black, must attract clients. If possible I want the front to be the logo and the back to show maybe the details.

Target Market(s)

Clients

Industry/Entity Type

Plumbing maintenance

Contact Information for Business Card

Name: Felix, Contact: 0461 539 207, Email: quandorplumbingsolutions@mailbrook.example, Licence number 728093K

Font styles to use
Other font styles liked:
• as per logo maybe?

Colors

Designer to choose colors to be used in the design.

Requirements
Nice to have
• stating the service I provide, emergency plumbing, plumbing maintenance, drainage maintenance, block sewer and stormwater, camera and locating.

```html
<!DOCTYPE html>
<html lang="en">
<head>
<meta charset="utf-8">
<title>Quandor Plumbing Solutions – Business Card</title>
<link href="https://fonts.googleapis.com/css2?family=Montserrat:wght@400;500;700&display=swap" rel="stylesheet">
<style>
  :root {
    --stage: #151515;
    --card: #1f1f1f;
    --blue: #4a90cc;
    --white: #f4f4f4;
    --text: #e6e6e6;
    --faint: #2d2d2d;
    --line-dark: #141414;
  }
  * { margin: 0; padding: 0; box-sizing: border-box; }
  html, body {
    width: 1200px; height: 1059px; overflow: hidden;
    background: var(--stage);
    font-family: "Montserrat", Arial, sans-serif;
  }
  .card {
    position: absolute; left: 255px; width: 690px; height: 392px;
    background: var(--card); border-radius: 16px; overflow: hidden;
    box-shadow: 0 14px 28px rgba(0,0,0,.55);
  }
  .card--front { top: 89px; }
  .card--back { top: 547px; }

  .brand {
    position: absolute; left: 44px; top: 152px; width: 220px;
    color: var(--white); font-weight: 700; font-size: 27px;
    line-height: 1.1; text-transform: uppercase; letter-spacing: .5px;
  }
  .brand__sub { font-size: 13px; letter-spacing: 1.3px; display: block; margin-top: 4px; }

  .divider {
    position: absolute; left: 278px; top: 120px; width: 2px; height: 151px;
    background: var(--blue);
  }
  .details { position: absolute; left: 300px; top: 118px; color: var(--text); white-space: nowrap; }
  .details__name { color: var(--blue); font-weight: 700; font-size: 25px; line-height: 1; }
  .details__role { font-size: 14px; margin-top: 3px; }
  .details__licence { font-size: 14px; margin-top: 15px; }
  .contact { list-style: none; margin-top: 14px; }
  .contact li { display: flex; align-items: center; font-size: 14px; height: 26px; }
  .contact svg { width: 13px; height: 13px; margin-right: 7px; flex: none; }

  .swoosh { position: absolute; left: 0; top: 0; width: 690px; height: 392px; }

  .brand--faint {
    position: absolute; left: 0; right: 0; top: 120px; text-align: center;
    color: var(--faint); font-weight: 700; font-size: 52px; line-height: 1.05;
    text-transform: uppercase;
  }
  .brand--faint span { display: block; font-size: 24px; letter-spacing: 2px; }

  .services {
    position: absolute; left: 0; right: 0; top: 308px; text-align: center;
    color: var(--text); font-size: 15px; line-height: 27px;
  }
  .services .dot { color: var(--blue); margin: 0 6px; }
</style>
</head>
<body>

<section class="card card--front">
  <div class="brand">Quandor<span class="brand__sub">Plumbing Solutions</span></div>
  <div class="divider"></div>
  <div class="details">
    <div class="details__name">FELIX</div>
    <div class="details__role">Founder &amp; CEO</div>
    <div class="details__licence">Licence number 728093K</div>
    <ul class="contact">
      <li>
        <svg viewBox="0 0 24 24" aria-hidden="true"><path fill="#4a90cc" d="M6.6 10.8a15.1 15.1 0 0 0 6.6 6.6l2.2-2.2c.3-.3.7-.4 1-.2 1.1.4 2.3.6 3.6.6.6 0 1 .4 1 1V20c0 .6-.4 1-1 1A17 17 0 0 1 3 4c0-.6.4-1 1-1h3.5c.6 0 1 .4 1 1 0 1.3.2 2.5.6 3.6.1.3 0 .7-.2 1z"/></svg>
        0461 539 207
      </li>
      <li>
        <svg viewBox="0 0 24 24" aria-hidden="true"><rect x="2" y="5" width="20" height="14" fill="#4a90cc"/><path d="M2 5l10 8 10-8" fill="none" stroke="#1f1f1f" stroke-width="2"/></svg>
        quandorplumbingsolutions@mailbrook.example
      </li>
      <li>
        <svg viewBox="0 0 24 24" aria-hidden="true"><circle cx="12" cy="12" r="11" fill="#4a90cc"/></svg>
        @QuandorPlumbingSolutions
      </li>
    </ul>
  </div>
  <svg class="swoosh" viewBox="0 0 690 392" aria-hidden="true">
    <path d="M0 316 Q300 372 690 372 L690 392 L0 392 Z" fill="#4a90cc"/>
    <path d="M270 356 Q480 381 690 361 L690 368 Q480 386 270 356 Z" fill="#141414"/>
    <path d="M270 355 Q480 372 690 349 L690 360 Q480 378 270 355 Z" fill="#f4f4f4"/>
  </svg>
</section>

<section class="card card--back">
  <div class="brand--faint">Quandor<span>Plumbing Solutions</span></div>
  <p class="services">
    Emergency plumbing<span class="dot">•</span>Plumbing maintenance<span class="dot">•</span>Drainage maintenance<br>
    Block sewer and stormwater<span class="dot">•</span>Camera and locating
  </p>
</section>

</body>
</html>
```